Brand new letterhead, business card, email signature etc.

We are a financial company in London, UK. Our website is www.marlowvane.com. We're wanting a complete remodel of the company colours, letter head, business cards, email signatures, etc. Looking to keep the same font for the company name. I have upload a colour palette that we want to work with. We're looking for company letterhead for outgoing letters/ correspondence, letterhead for internal documentation, email signatures, e-letters. etc. Ultimately we will redesign the entire website also. It is important that our clients get a strong, secure, warm, trustworthy, solid feeling and first impression.
Updates

Designs look the same

Target Market(s)

Institutional investors, (ultra) high net worth individuals

Industry/Entity Type

Finance, Invesments banking.

Font styles to use
Other font styles liked:
• Current font is "Champagne & Limousines"

Requirements
Must have
• Must use the colours provided on the PDF uploaded to the portal. The purple = main colour. The red = accent colour.
Nice to have
• Nice to use same font as now for the company name "Corvane". Font is "Champagne & Limousines". Nice to have some reference to the old logo flower, but only subtle.
Should not have
• Do not use the colour red from our website. Use the colours provided on the colour palette PDF that I uploaded in the portal.

```html
<!DOCTYPE html>
<html lang="en">
<head>
<meta charset="utf-8">
<title>Corvane Stationery Set</title>
<link rel="stylesheet" href="https://fonts.googleapis.com/css2?family=Quicksand:wght@300;400;500;600&display=swap">
<style>
  :root {
    --board: #c8c8c0;
    --paper: #ffffff;
    --accent-red: #e03826;
    --brand-plum: #2e0f1e;
    --card-sand: #e0d9ce;
    --text-plum: #2e0f1e;
    --text-soft: #4a3a40;
    --label-grey: #4f4f4f;
    --rule: #d9d6cf;
  }
  * { box-sizing: border-box; margin: 0; padding: 0; }
  html, body { width: 1112px; height: 1200px; overflow: hidden; }
  body {
    position: relative;
    background: var(--board);
    font-family: "Quicksand", sans-serif;
    color: var(--text-soft);
  }
  .piece {
    position: absolute;
    background: var(--paper);
    overflow: hidden;
    box-shadow: 0 2px 6px rgba(0,0,0,0.18);
  }
  .top-band { position: absolute; left: 0; top: 0; width: 100%; background: var(--accent-red); }
  .icon-column { position: absolute; top: 0; background: var(--brand-plum); }
  .icon-column .split { position: absolute; left: 0; width: 100%; height: 1px; background: rgba(255,255,255,0.35); }
  .icon { position: absolute; fill: #fff; }
  .contact { position: absolute; text-align: right; font-weight: 300; color: var(--text-soft); white-space: nowrap; }
  .rule { position: absolute; height: 1px; background: var(--rule); }
  .wordmark { position: absolute; display: flex; align-items: center; }
  .wordmark .mark-square { border: 1px solid var(--brand-plum); background: var(--paper); flex: none; }
  .wordmark .name {
    font-weight: 300; color: var(--text-plum);
    text-transform: uppercase; line-height: 1;
  }
  .person { position: absolute; color: var(--text-plum); line-height: 1; }
  .person .full-name { font-weight: 600; display: block; }
  .person .role { font-weight: 500; display: block; }
  .piece-label {
    position: absolute; font-size: 10px; font-weight: 400;
    color: var(--label-grey); text-align: right; white-space: nowrap;
  }

  /* Letterhead */
  .letterhead { left: 87px; top: 78px; width: 764px; height: 1036px; }
  .letterhead .top-band { height: 33px; }
  .letterhead .icon-column { left: 689px; width: 40px; height: 215px; }
  .letterhead .contact { right: 86px; font-size: 12.5px; line-height: 15.5px; }
  .letterhead .rule { left: 507px; width: 182px; }
  .letterhead .icon { width: 16px; height: 16px; left: 12px; }
  .letterhead .wordmark { left: 59px; top: 91px; height: 51px; }
  .letterhead .mark-square { width: 51px; height: 51px; }
  .letterhead .name { font-size: 31px; letter-spacing: 6px; margin-left: 12px; }

  /* Business cards & signature, shared scale */
  .card, .signature { height: 188px; }
  .card .top-band, .signature .top-band { height: 14px; }
  .card .icon-column, .signature .icon-column { width: 22px; height: 104px; }
  .card .contact, .signature .contact { font-size: 7px; line-height: 9.5px; }
  .card .rule, .signature .rule { width: 100px; }
  .card .icon, .signature .icon { width: 10px; height: 10px; left: 6px; }
  .card .mark-square, .signature .mark-square { width: 30px; height: 30px; }
  .card .name, .signature .name { font-size: 18px; letter-spacing: 3.5px; margin-left: 7px; }
  .card .full-name, .signature .full-name { font-size: 11px; }
  .card .role, .signature .role { font-size: 6.5px; margin-top: 1px; }

  .card-front { left: 693px; top: 427px; width: 330px; }
  .card-front .icon-column { left: 291px; }
  .card-front .contact { right: 45px; }
  .card-front .rule { left: 191px; }
  .card-front .wordmark { left: 17px; top: 142px; }
  .card-front .person { left: 17px; top: 458px; }

  .card-back { left: 694px; top: 647px; width: 330px; background: var(--card-sand); }
  .card-back .mark-panel {
    position: absolute; left: 109px; top: 30px; width: 109px; height: 109px;
    background: var(--paper); border: 4px solid var(--paper); outline: 1px solid var(--brand-plum); outline-offset: -6px;
  }
  .card-back .web-address {
    position: absolute; left: 0; width: 100%; top: 148px; text-align: center;
    font-size: 8.5px; letter-spacing: 3.6px; font-weight: 500; color: var(--brand-plum);
  }

  .signature { left: 509px; top: 873px; width: 518px; }
  .signature .icon-column { left: 479px; }
  .signature .contact { right: 44px; }
  .signature .rule { left: 379px; }
  .signature .wordmark { left: 22px; top: 31px; }
</style>
</head>
<body>
<svg width="0" height="0" style="position:absolute" aria-hidden="true">
  <defs>
    <symbol id="icon-phone" viewBox="0 0 24 24">
      <path d="M2 9c0-3 5-5 10-5s10 2 10 5v2h-5V8.5c-1.5-.6-3.2-.9-5-.9s-3.5.3-5 .9V11H2z"/>
      <path d="M6 12l2-3h8l2 3v7H6z M9 13h1.5v1.5H9z M11.25 13h1.5v1.5h-1.5z M13.5 13H15v1.5h-1.5z M9 15.5h1.5V17H9z M11.25 15.5h1.5V17h-1.5z M13.5 15.5H15V17h-1.5z" fill-rule="evenodd"/>
    </symbol>
    <symbol id="icon-globe" viewBox="0 0 24 24">
      <g fill="none" stroke="#fff" stroke-width="1.8">
        <circle cx="12" cy="12" r="9.5"/>
        <path d="M4 7c4 2 6 6 5 14M20 7c-5 1-9 5-11 12M3 13c5-2 12-1 18 2M9 3c3 4 6 9 7 17"/>
      </g>
    </symbol>
    <symbol id="icon-pin" viewBox="0 0 24 24">
      <path d="M12 1.5c-4.4 0-8 3.4-8 7.8 0 5.6 8 13.2 8 13.2s8-7.6 8-13.2c0-4.4-3.6-7.8-8-7.8zm0 10.8a3 3 0 1 1 0-6 3 3 0 0 1 0 6z"/>
    </symbol>
  </defs>
</svg>

<!-- Letterhead -->
<section class="piece letterhead">
  <div class="top-band"></div>
  <div class="wordmark">
    <span class="mark-square"></span>
    <span class="name">Corvane</span>
  </div>
  <div class="contact" style="top:88px">+000 12345 6789<br>+000 12345 6789</div>
  <div class="rule" style="top:131px"></div>
  <div class="contact" style="top:137px">urwebsitename.com<br>urname@email.com</div>
  <div class="rule" style="top:175px"></div>
  <div class="contact" style="top:185px">1234 Street name, town/city,<br>state/country, post/zip 012345.</div>
  <div class="icon-column">
    <span class="split" style="top:131px"></span>
    <span class="split" style="top:175px"></span>
    <svg class="icon" style="top:96px"><use href="#icon-phone"/></svg>
    <svg class="icon" style="top:144px"><use href="#icon-globe"/></svg>
    <svg class="icon" style="top:192px"><use href="#icon-pin"/></svg>
  </div>
</section>

<!-- Business card front -->
<p class="piece-label" style="right:90px; top:409px">Business card front</p>
<section class="piece card card-front">
  <div class="top-band"></div>
  <div class="person" style="top:30px">
    <span class="full-name">Elliot Harcourt</span>
    <span class="role">Designation</span>
  </div>
  <div class="contact" style="top:30px">+000 12345 6789<br>+000 12345 6789</div>
  <div class="rule" style="top:53px"></div>
  <div class="contact" style="top:57px">urwebsitename.com<br>urname@email.com</div>
  <div class="rule" style="top:78px"></div>
  <div class="contact" style="top:83px">1234 Street name, town/city,<br>state/country, post/zip 012345.</div>
  <div class="icon-column">
    <svg class="icon" style="top:34px"><use href="#icon-phone"/></svg>
    <svg class="icon" style="top:60px"><use href="#icon-globe"/></svg>
    <svg class="icon" style="top:87px"><use href="#icon-pin"/></svg>
  </div>
  <div class="wordmark">
    <span class="mark-square"></span>
    <span class="name">Corvane</span>
  </div>
</section>

<!-- Business card back -->
<p class="piece-label" style="right:88px; top:633px">Business card back</p>
<section class="piece card card-back">
  <div class="mark-panel"></div>
  <p class="web-address">www.marlowvane.com</p>
</section>

<!-- Email signature -->
<p class="piece-label" style="right:85px; top:857px">Email Signature</p>
<section class="piece signature">
  <div class="top-band"></div>
  <div class="wordmark">
    <span class="mark-square"></span>
    <span class="name">Corvane</span>
  </div>
  <div class="contact" style="top:30px">+000 12345 6789<br>+000 12345 6789</div>
  <div class="rule" style="top:52px"></div>
  <div class="contact" style="top:56px">urwebsitename.com<br>urname@email.com</div>
  <div class="rule" style="top:78px"></div>
  <div class="contact" style="top:83px">1234 Street name, town/city,<br>state/country, post/zip 012345.</div>
  <div class="icon-column">
    <svg class="icon" style="top:34px"><use href="#icon-phone"/></svg>
    <svg class="icon" style="top:59px"><use href="#icon-globe"/></svg>
    <svg class="icon" style="top:86px"><use href="#icon-pin"/></svg>
  </div>
  <div class="person" style="left:22px; top:150px">
    <span class="full-name">Elliot Harcourt</span>
    <span class="role">Designation</span>
  </div>
</section>
</body>
</html>
```